855 Bright Owl

Redesigning this front and back business card flyer and keeping the info but making it look better.

This is all about using the info and logo on the business card design and creating a better layout using any of the following and more.

Changing the background color or imagine, chaining the placement of content, resizing content.

Target Market(s)

Targeting people that have been injured on one side and people that have been giving a DUI on the other.

Contact Information for Business Card

We are looking to keep the info but make it look a fee cleaner and less cluttered

Font styles to use
Sans Serif

Requirements
Must have
• Must have the same info but a better layout.
Nice to have
• better background colors or image or layout. different fonts or same font all design options that will make it look professional and clean.

```html
<!DOCTYPE html>
<html lang="en">
<head>
<meta charset="utf-8">
<title>855 Bright Owl – Business Cards</title>
<link href="https://fonts.googleapis.com/css2?family=Arimo:wght@400;700&family=Archivo+Black&display=swap" rel="stylesheet">
<style>
  :root {
    --bg: #dcdfe2;
    --black: #0b0b0b;
    --red: #d3202a;
    --red-dark: #b81c24;
    --white: #ffffff;
    --ink: #1a1a1a;
    --grey-text: #e6e6e6;
  }
  * { box-sizing: border-box; margin: 0; padding: 0; }
  html, body { width: 1200px; height: 800px; overflow: hidden; }
  body {
    background: var(--bg);
    font-family: "Arimo", Arial, sans-serif;
    position: relative;
  }
  .card {
    position: absolute;
    width: 640px;
    height: 366px;
    overflow: hidden;
    box-shadow: 0 6px 18px rgba(0,0,0,0.18);
  }

  /* ---------- Injury card ---------- */
  .card-injury { left: 470px; top: 30px; background: var(--black); color: var(--white); }
  .brand-strip {
    position: absolute; top: 0; bottom: 0; width: 84px;
    display: flex; align-items: center; justify-content: center;
  }
  .brand-name {
    writing-mode: vertical-rl;
    font-family: "Arimo", Arial, sans-serif;
    font-weight: 700;
    font-size: 38px;
    letter-spacing: 1px;
    color: var(--white);
    white-space: nowrap;
  }
  .card-injury .brand-strip { left: 0; }
  .injury-copy { position: absolute; left: 104px; top: 30px; width: 340px; }
  .injury-lead { font-size: 23px; font-weight: 700; line-height: 1.05; }
  .injury-headline {
    font-family: "Archivo Black", Arial, sans-serif;
    font-size: 36px; color: var(--red); line-height: 1.05; margin-bottom: 10px;
  }
  .point-list { list-style: none; }
  .point-list li {
    position: relative; padding-left: 16px; line-height: 1.2;
  }
  .point-list li::before {
    content: ""; position: absolute; left: 0; top: 0.3em;
    border-left: 9px solid var(--red);
    border-top: 5px solid transparent; border-bottom: 5px solid transparent;
  }
  .injury-points li { font-size: 15px; color: var(--grey-text); }
  .injury-promise { font-size: 17px; font-weight: 700; line-height: 1.25; margin: 14px 0 12px; }
  .phone-row { display: flex; align-items: center; gap: 10px; }
  .phone-icon { width: 34px; height: 34px; flex: none; }
  .phone-number { font-weight: 700; font-size: 32px; letter-spacing: 0.5px; }
  .web-address { font-size: 18px; margin-top: 4px; }
  .web-address strong { font-weight: 700; }

  .photo-column {
    position: absolute; right: 14px; top: 30px; width: 152px;
    display: flex; flex-direction: column; gap: 6px;
  }
  .photo { height: 96px; }
  .photo-crash { background: linear-gradient(135deg, #1a1420 0%, #5a2030 45%, #8f8f9a 70%, #201a24 100%); }
  .photo-boot { background: linear-gradient(180deg, #c9c9c9 0%, #8a8c90 60%, #4a4c52 100%); }
  .photo-wheelchair { background: linear-gradient(90deg, #1c1c1e 0%, #56595e 55%, #9a9ca0 75%, #2a2a2c 100%); }

  /* ---------- DUI card ---------- */
  .card-dui { left: 110px; top: 410px; background: var(--white); }
  .dui-panel {
    position: absolute; left: 0; top: 0; bottom: 0; width: 250px;
    background: linear-gradient(180deg, var(--red) 0%, var(--red-dark) 100%);
    color: var(--white); padding: 30px 22px;
  }
  .dui-question { font-size: 22px; font-weight: 700; line-height: 1.15; margin-bottom: 34px; }
  .dui-headline {
    font-family: "Archivo Black", Arial, sans-serif;
    font-size: 40px; line-height: 1.0; text-transform: uppercase;
  }
  .dui-copy { position: absolute; left: 268px; top: 30px; width: 282px; color: var(--ink); }
  .dui-points li { font-size: 13.5px; margin-bottom: 1px; }
  .dui-copy .phone-row { margin-top: 26px; }
  .dui-copy .phone-number { font-size: 30px; }
  .dui-copy .web-address { font-size: 17px; }
  .card-dui .brand-strip { right: 0; background: var(--black); width: 76px; }
  .card-dui .brand-name { transform: rotate(180deg); font-size: 36px; }
</style>
</head>
<body>

<section class="card card-injury">
  <div class="brand-strip"><span class="brand-name">855 Bright Owl</span></div>
  <div class="injury-copy">
    <p class="injury-lead">If You’ve Been Injured</p>
    <h1 class="injury-headline">DON’T GIVE IN</h1>
    <ul class="point-list injury-points">
      <li>to an inexperienced lawyer!</li>
      <li>for less than you deserve!</li>
      <li>to paying massive medical bills!</li>
      <li>to a life of pain and debt!</li>
    </ul>
    <p class="injury-promise">We fight for you, so you<br>can focus on getting better</p>
    <div class="phone-row">
      <svg class="phone-icon" viewBox="0 0 34 34" aria-hidden="true">
        <circle cx="17" cy="17" r="17" fill="#d3202a"/>
        <path d="M12 9c1-.6 2-.3 2.5.6l1.6 2.9c.4.8.2 1.7-.5 2.2l-1.2.9c.8 1.8 2.1 3.2 3.9 4.1l.9-1.2c.5-.7 1.5-.9 2.2-.4l2.8 1.7c.9.5 1.1 1.6.5 2.5l-1 1.4c-.7 1-2 1.4-3.1 1-5-1.7-8.6-5.4-10.2-10.4-.4-1.2 0-2.4 1-3.1z" fill="#fff"/>
      </svg>
      <span class="phone-number">855-555-0148</span>
    </div>
    <p class="web-address">www.<strong>855brightowl</strong>.com</p>
  </div>
  <div class="photo-column">
    <div class="photo photo-crash" role="img" aria-label="Photo of a damaged car at a night-time accident scene"></div>
    <div class="photo photo-boot" role="img" aria-label="Photo of an injured leg in a medical walking boot with crutches"></div>
    <div class="photo photo-wheelchair" role="img" aria-label="Photo of a silhouetted person in a wheelchair by a window"></div>
  </div>
</section>

<section class="card card-dui">
  <div class="dui-panel">
    <p class="dui-question">What Should<br>I Do If I Get<br>Pulled Over<br>For Dui?</p>
    <h2 class="dui-headline">Don’t<br>Give In<br>To a<br>DUI</h2>
  </div>
  <div class="dui-copy">
    <ul class="point-list dui-points">
      <li>Pull over in a calm, normal manner</li>
      <li>Be polite at all times</li>
      <li>Do not admit to drinking</li>
      <li>Do not submit to any field sobriety tests</li>
      <li>Do not submit to taking a chemical test (breath, blood or urine)</li>
      <li>Do not make any statement after being arrested, especially when placed in the police cruiser</li>
    </ul>
    <div class="phone-row">
      <svg class="phone-icon" viewBox="0 0 34 34" aria-hidden="true">
        <circle cx="17" cy="17" r="17" fill="#d3202a"/>
        <path d="M12 9c1-.6 2-.3 2.5.6l1.6 2.9c.4.8.2 1.7-.5 2.2l-1.2.9c.8 1.8 2.1 3.2 3.9 4.1l.9-1.2c.5-.7 1.5-.9 2.2-.4l2.8 1.7c.9.5 1.1 1.6.5 2.5l-1 1.4c-.7 1-2 1.4-3.1 1-5-1.7-8.6-5.4-10.2-10.4-.4-1.2 0-2.4 1-3.1z" fill="#fff"/>
      </svg>
      <span class="phone-number">855-555-0148</span>
    </div>
    <p class="web-address">www.<strong>855brightowl</strong>.com</p>
  </div>
  <div class="brand-strip"><span class="brand-name">855 Bright Owl</span></div>
</section>

</body>
</html>
```